Birchline Septic Solutions

Would like to see some single sided ones but would also like to see some double sided with one sided only being the logo. Owners name is Colin Vandro. Phone number is 555-214-0387
Services are pumping, inspections, installs, and repairs

Contact Information for Business Card

555-241-0387 Colin Vandro Cedarvale, KS

```html
<!DOCTYPE html>
<html lang="en">
<head>
<meta charset="UTF-8">
<title>Birchline Septic Solutions – Business Cards</title>
<link href="https://fonts.googleapis.com/css2?family=Gelasio:wght@400&display=swap" rel="stylesheet">
<style>
  :root {
    --page-bg: #e9e6e1;
    --card-bg: #050607;
    --forest-dark: #1a1c1d;
    --forest-mid: #111314;
    --teal: #25b0ab;
    --ink: #f2f2f2;
    --card-w: 600px;
    --card-h: 343px;
  }
  * { box-sizing: border-box; margin: 0; padding: 0; }
  html, body {
    width: 1200px; height: 900px; overflow: hidden;
    background: var(--page-bg);
    font-family: "Gelasio", Georgia, serif;
  }
  h2 { font-weight: 400; }
  .sheet {
    position: relative; width: 1200px; height: 900px;
  }
  .card {
    position: absolute; left: 300px;
    width: var(--card-w); height: var(--card-h);
    background: var(--card-bg);
    border-radius: 34px;
    overflow: hidden;
    box-shadow: 0 14px 30px rgba(0,0,0,.25);
  }
  .card--services { top: 70px; }
  .card--contact { top: 487px; }

  .forest-band {
    position: absolute; left: 0; right: 0; bottom: 0; height: 52%;
    background: linear-gradient(to bottom, rgba(26,28,29,0) 0%, var(--forest-mid) 35%, var(--forest-dark) 100%);
  }

  .brand {
    position: absolute; left: 48px; top: 104px; width: 270px;
    color: var(--ink); font-weight: 400; text-align: center;
  }
  .brand__mark {
    display: block; width: 14px; height: 14px; margin: 0 auto 10px;
    background: var(--ink); border-radius: 50%;
  }
  .brand__name { font-size: 46px; line-height: 1; letter-spacing: .5px; }
  .brand__sub { font-size: 17px; letter-spacing: 4px; margin-top: 10px; text-transform: uppercase; }

  .divider {
    position: absolute; left: 340px; top: 62px; width: 1.5px; height: 180px;
    background: var(--teal);
  }
  .info {
    position: absolute; left: 372px; top: 66px; color: var(--ink);
  }
  .info__heading {
    color: var(--teal); font-size: 15px; letter-spacing: .6px; text-transform: uppercase;
    margin-bottom: 10px;
  }
  .service-list { list-style: none; }
  .service-list li {
    display: flex; align-items: center; gap: 8px;
    font-size: 16px; line-height: 24px;
  }
  .icon { width: 14px; height: 14px; flex: none; }

  .person__name { color: var(--teal); font-size: 22px; text-transform: uppercase; letter-spacing: .3px; }
  .person__role { font-size: 16px; margin-bottom: 18px; }
  .contact-list { list-style: none; padding-left: 22px; }
  .contact-list li {
    display: flex; align-items: center; gap: 10px;
    font-size: 17px; line-height: 28px;
  }
</style>
</head>
<body>
<main class="sheet">

  <section class="card card--services">
    <div class="forest-band" role="img" aria-label="Pine forest silhouette along the bottom of the card"></div>
    <div class="brand">
      <span class="brand__mark"></span>
      <div class="brand__name">Birchline</div>
      <div class="brand__sub">Septic Solutions</div>
    </div>
    <div class="divider"></div>
    <div class="info">
      <h2 class="info__heading">Our Services</h2>
      <ul class="service-list">
        <li><svg class="icon" viewBox="0 0 14 14"><path d="M2 7.5 L5.5 11 L12 3" fill="none" stroke="#25b0ab" stroke-width="2"/></svg>Pumping</li>
        <li><svg class="icon" viewBox="0 0 14 14"><path d="M2 7.5 L5.5 11 L12 3" fill="none" stroke="#25b0ab" stroke-width="2"/></svg>Inspections</li>
        <li><svg class="icon" viewBox="0 0 14 14"><path d="M2 7.5 L5.5 11 L12 3" fill="none" stroke="#25b0ab" stroke-width="2"/></svg>Installs And</li>
        <li><svg class="icon" viewBox="0 0 14 14"><path d="M2 7.5 L5.5 11 L12 3" fill="none" stroke="#25b0ab" stroke-width="2"/></svg>Repairs</li>
      </ul>
    </div>
  </section>

  <section class="card card--contact">
    <div class="forest-band" role="img" aria-label="Pine forest silhouette along the bottom of the card"></div>
    <div class="brand">
      <span class="brand__mark"></span>
      <div class="brand__name">Birchline</div>
      <div class="brand__sub">Septic Solutions</div>
    </div>
    <div class="divider"></div>
    <div class="info">
      <h2 class="person__name">Colin Vandro</h2>
      <p class="person__role">Owners</p>
      <ul class="contact-list">
        <li><svg class="icon" viewBox="0 0 14 14"><path d="M3 1.5 L5.5 1.5 L6.5 4.5 L5 5.8 Q6.3 8.4 8.2 9 L9.5 7.5 L12.5 8.5 L12.5 11 Q12 12.5 10.5 12.5 Q2 11.5 1.5 3.5 Q1.5 2 3 1.5 Z" fill="#25b0ab"/></svg>555-241-0387</li>
        <li><svg class="icon" viewBox="0 0 14 14"><path d="M7 13 Q2 7.5 2 5.2 A5 5 0 0 1 12 5.2 Q12 7.5 7 13 Z" fill="#25b0ab"/><circle cx="7" cy="5.2" r="1.9" fill="#050607"/></svg>Cedarvale, KS</li>
      </ul>
    </div>
  </section>

</main>
</body>
</html>
```